Business Card Design Project

We are looking for a new business card design to go with our new logo. We need to have a front and back card with our name and numberous phone numbers on the front and our addresses on the back. We will need to be able to edit the cards to have different names and numbers. Right now our card looks too busy and cluttered. We need to have our Brightmoor Estates Group Logo Prominently displayed. We will also need the Halvern Dunstead Portland Central, the relator logo and the equal housing logo on the front somewhere. We would like to have our addresses on the back along with the quote "Our most important goal is to exceed the expectations of our clients and the finest compliment we can received is a referral from a friend or past client. Thank you for your support!" Also, we would like the "Please follow us on : facebook logo, twitter loto, youtube logo and wordpress logo" I've attached our new logo and what our current business card looks like.

```html
<!DOCTYPE html>
<html lang="en">
<head>
<meta charset="utf-8">
<title>Brightmoor Estates Group – Business Card</title>
<link rel="stylesheet" href="https://fonts.googleapis.com/css2?family=Source+Sans+3:wght@400;600;700&display=swap">
<style>
  :root {
    --stage: #e9e6e2;
    --card: #ffffff;
    --card-edge: #3c3c3c;
    --brand-red: #c0272d;
    --brand-red-dark: #9e1e24;
    --ink: #2a2a2a;
    --ink-soft: #3d3d3d;
    --rule: #c9c9c9;
    --band-grey: #5f6063;
    --band-grey-light: #8a8b8e;
    --social-tile: #9a9a9a;
  }
  * { box-sizing: border-box; margin: 0; padding: 0; }
  html, body {
    width: 1200px; height: 1027px; overflow: hidden;
    background: var(--stage);
    font-family: "Source Sans 3", "Myriad Pro", Arial, sans-serif;
    color: var(--ink);
  }
  .canvas { position: relative; width: 1200px; height: 1027px; }

  .card {
    position: absolute;
    width: 740px; height: 422px;
    background: var(--card);
    border: 1px solid var(--card-edge);
    border-radius: 24px;
    overflow: hidden;
  }
  .card--front { left: 56px; top: 52px; }
  .card--back { left: 376px; top: 531px; }

  /* brand name block (stands where the logo sits) */
  .brand {
    position: absolute;
    display: flex; flex-direction: column; align-items: center;
    text-align: center;
  }
  .brand__dot {
    width: 54px; height: 54px; border-radius: 50%;
    background: var(--brand-red);
    margin-bottom: 16px;
  }
  .brand__name {
    font-weight: 600;
    font-size: 38px;
    line-height: 1.02;
    color: var(--ink-soft);
  }
  .card--front .brand { left: 30px; top: 86px; width: 320px; }
  .card--back .brand { left: 210px; top: 62px; width: 320px; }

  .front__divider {
    position: absolute; left: 397px; top: 56px;
    width: 1px; height: 268px; background: var(--rule);
  }
  .contact { position: absolute; left: 418px; top: 54px; }
  .contact__name { font-weight: 700; font-size: 21px; color: var(--brand-red); line-height: 1.2; }
  .contact__title { font-size: 17px; color: var(--brand-red); line-height: 1.25; }
  .contact__address { margin-top: 14px; font-size: 17px; line-height: 24px; color: var(--ink); }
  .contact__lines { margin-top: 16px; list-style: none; font-size: 17px; line-height: 25px; }
  .contact__lines li { display: flex; align-items: center; gap: 7px; }
  .contact__lines svg { width: 13px; height: 13px; flex: none; fill: var(--ink); }

  .front__band { position: absolute; left: 0; bottom: 0; width: 740px; height: 130px; }
  .front__web {
    position: absolute; left: 48px; bottom: 24px;
    color: #ffffff; font-size: 17px; letter-spacing: 3.6px;
  }

  .social { position: absolute; left: 184px; top: 298px; display: flex; gap: 19px; }
  .social__tile {
    width: 81px; height: 81px; border-radius: 12px;
    background: var(--social-tile);
  }
</style>
</head>
<body>
<div class="canvas">

  <section class="card card--front" aria-label="Card front">
    <div class="brand">
      <span class="brand__dot"></span>
      <span class="brand__name">Brightmoor<br>Estates Group</span>
    </div>

    <div class="front__divider"></div>

    <div class="contact">
      <p class="contact__name">Dana Whitcombe</p>
      <p class="contact__title">Broker, Listing Specialist</p>
      <p class="contact__address">118 Harbor Plaza<br>5200 SE Alder Ave, #310<br>Portland, OR 97230</p>
      <ul class="contact__lines">
        <li><svg viewBox="0 0 16 16" aria-hidden="true"><path d="M8 0a8 8 0 1 0 0 16A8 8 0 0 0 8 0zm0 1.6a6.4 6.4 0 1 1 0 12.8A6.4 6.4 0 0 1 8 1.6zM5.2 4.2l1.5-.4 1 2.2-.9.8c.4 1 1.2 1.8 2.2 2.3l.8-.9 2.2 1-.4 1.5c-3 .2-6.5-3.4-6.4-6.5z"/></svg>(503) 555-0142(office)</li>
        <li><svg viewBox="0 0 16 16" aria-hidden="true"><path d="M8 0a8 8 0 1 0 0 16A8 8 0 0 0 8 0zm0 1.6a6.4 6.4 0 1 1 0 12.8A6.4 6.4 0 0 1 8 1.6zM5.2 4.2l1.5-.4 1 2.2-.9.8c.4 1 1.2 1.8 2.2 2.3l.8-.9 2.2 1-.4 1.5c-3 .2-6.5-3.4-6.4-6.5z"/></svg>(800) 555-0187</li>
        <li><svg viewBox="0 0 16 16" aria-hidden="true"><path d="M4.5 1h7a1 1 0 0 1 1 1v12a1 1 0 0 1-1 1h-7a1 1 0 0 1-1-1V2a1 1 0 0 1 1-1zm1 2v6h5V3zm0 7.5v1.5h5v-1.5z"/></svg>(503) 555-0163</li>
        <li><svg viewBox="0 0 16 16" aria-hidden="true"><path d="M4 1h6l2 2v3H4zM1 7h14v6h-2v2H3v-2H1zm4 4v3h6v-3z"/></svg>(503) 555-0129</li>
        <li><svg viewBox="0 0 16 16" aria-hidden="true"><path d="M1 3h14v10H1zm1.5 1.3v.4L8 8.4l5.5-3.7v-.4z"/></svg>dana@brightmoorestates.com</li>
      </ul>
    </div>

    <svg class="front__band" viewBox="0 0 740 130" preserveAspectRatio="none" aria-hidden="true">
      <defs>
        <linearGradient id="bandGrey" x1="0" y1="0" x2="1" y2="0">
          <stop offset="0" stop-color="var(--band-grey)"/>
          <stop offset="1" stop-color="var(--band-grey-light)"/>
        </linearGradient>
      </defs>
      <path d="M0 26 C120 -4 260 6 410 54 C520 88 620 70 740 32 L740 130 L0 130 Z" fill="var(--brand-red)"/>
      <path d="M0 34 C130 8 270 24 400 64 C520 98 630 82 740 44 L740 130 L0 130 Z" fill="#ffffff"/>
      <path d="M0 46 C140 24 270 42 390 78 C520 112 640 100 740 60 L740 130 L0 130 Z" fill="url(#bandGrey)"/>
    </svg>
    <p class="front__web">www.brightmoorestates.com</p>
  </section>

  <section class="card card--back" aria-label="Card back">
    <div class="brand">
      <span class="brand__dot"></span>
      <span class="brand__name">Brightmoor<br>Estates Group</span>
    </div>
    <div class="social" role="img" aria-label="Social network links">
      <span class="social__tile"></span>
      <span class="social__tile"></span>
      <span class="social__tile"></span>
      <span class="social__tile"></span>
    </div>
  </section>

</div>
</body>
</html>
```